BrivoTerna. Lantern of the Steady Harvest. Business card

Professional business card for BrivoTerna (Lantern of the Steady Harvest)
My rationale: Strategy-> Execution-> Results-> Value that lead to the BrivoTerna name: We put the Lantern of the Steady Harvest.
We deliver value to our customers helping them at defining a good strategy (cyan arrow). 90% of well formulated strategies fail due to poor execution so we also consider strategical execution very important (green arrow). Due to the execution we obtain the results (blue arrow). Finally, the results provide feedback to redefine strategy, and the new strategy has to be executed and new results obtained providing new feedback and on and on. It's like a wheel that finally, must create corporate value: value for shareholders, staholders, employees, providers...-

Target Market(s)

CEOs and steering comitees , invewrnent funds

Industry/Entity Type

Business Consultant

Contact Information for Business Card

Teodoro Vinsquel
CEO & Founder
teodoro.vinsquel@brivoterna-example.com
Mobile: +34 655.803.912
www.brivoterna-example.com

Colors

Designer to choose colors to be used in the design.

Requirements
Nice to have
• Nice to hace the words: Strategy, execution, results
• Nice to vave the claim: Lantern of the Steady Harvest
• The three colors should be shown:
• cyan for STRATEGY
• green for EXECUTION
• blue for RESULTS
Should not have
• Complete black background

```html
<!DOCTYPE html>
<html lang="en">
<head>
<meta charset="utf-8">
<title>BrivoTerna – Business Card</title>
<link rel="stylesheet" href="https://fonts.googleapis.com/css2?family=Montserrat:wght@400;700&family=Raleway:wght@400;500&display=swap">
<style>
  :root {
    --brand-blue: #233f91;
    --brand-green: #8cc63f;
    --brand-cyan: #29abe2;
    --card-white: #ffffff;
    --text-grey: #4a4a4a;
    --backdrop: #e9e6e1;
  }
  * { box-sizing: border-box; margin: 0; padding: 0; }
  html, body {
    width: 1200px; height: 909px; overflow: hidden;
    background: var(--backdrop);
  }
  .sheet {
    width: 1200px; height: 909px;
    display: flex; flex-direction: column;
    align-items: center; justify-content: center; gap: 56px;
  }
  .card {
    position: relative;
    width: 640px; height: 366px;
    border-radius: 22px; overflow: hidden;
    box-shadow: 0 6px 18px rgba(0,0,0,0.18);
  }
  .card--front {
    background: var(--brand-blue);
    display: flex; align-items: center; justify-content: center;
  }
  .wordmark {
    display: flex; align-items: center; gap: 14px;
    font-family: "Montserrat", sans-serif;
    font-weight: 700; letter-spacing: -0.5px;
  }
  .wordmark__dot { border-radius: 50%; flex: none; }
  .card--front .wordmark { font-size: 64px; color: var(--card-white); }
  .card--front .wordmark__dot { width: 22px; height: 22px; background: var(--card-white); }

  .card--back { background: var(--card-white); }
  .card__wave { position: absolute; inset: 0; width: 100%; height: 100%; }
  .card--back .wordmark {
    position: absolute; left: 48px; top: 150px;
    font-size: 40px; color: var(--brand-blue); gap: 10px;
  }
  .card--back .wordmark__dot { width: 14px; height: 14px; background: var(--brand-blue); }
  .divider {
    position: absolute; left: 318px; top: 40px;
    width: 1.5px; height: 150px; background: var(--brand-green);
  }
  .contact {
    position: absolute; left: 338px; top: 40px;
    font-family: "Raleway", sans-serif; color: var(--text-grey);
  }
  .contact__name {
    font-family: "Montserrat", sans-serif; font-weight: 700;
    font-size: 24px; color: var(--brand-green); line-height: 1.1;
  }
  .contact__role { font-size: 15px; margin: 4px 0 12px; }
  .contact__list { list-style: none; font-size: 13.5px; line-height: 1.75; }
  .contact__list li { display: flex; align-items: center; gap: 8px; white-space: nowrap; }
  .contact__icon { width: 11px; height: 11px; flex: none; }
</style>
</head>
<body>
<main class="sheet">

  <section class="card card--front" aria-label="Card front">
    <div class="wordmark"><span class="wordmark__dot"></span>BrivoTerna</div>
  </section>

  <section class="card card--back" aria-label="Card back">
    <svg class="card__wave" viewBox="0 0 640 366" preserveAspectRatio="none" aria-hidden="true">
      <path d="M0,366 L0,353 C170,343 300,272 410,245 C510,222 585,217 640,215 L640,366 Z" fill="var(--brand-blue)"/>
      <path d="M0,344 C170,334 300,263 410,236 C510,213 585,208 640,206" fill="none" stroke="var(--brand-green)" stroke-width="3.5"/>
      <path d="M0,336 C170,326 300,255 410,228 C510,205 585,200 640,198" fill="none" stroke="var(--brand-cyan)" stroke-width="3.5"/>
    </svg>

    <div class="wordmark"><span class="wordmark__dot"></span>BrivoTerna</div>

    <div class="divider"></div>

    <div class="contact">
      <p class="contact__name">Teodoro Vinsquel</p>
      <p class="contact__role">CEO &amp; Founder</p>
      <ul class="contact__list">
        <li>
          <svg class="contact__icon" viewBox="0 0 12 12"><rect x="3" y="0.5" width="6" height="11" rx="1.2" fill="none" stroke="var(--brand-blue)" stroke-width="1.3"/><circle cx="6" cy="9.5" r="0.8" fill="var(--brand-blue)"/></svg>
          +34 655.803.912
        </li>
        <li>
          <svg class="contact__icon" viewBox="0 0 12 12"><rect x="0.5" y="2.5" width="11" height="7.5" fill="var(--brand-blue)"/><path d="M0.5,2.5 L6,7 L11.5,2.5" fill="none" stroke="#fff" stroke-width="1"/></svg>
          teodoro.vinsquel@brivoterna-example.com
        </li>
        <li>
          <svg class="contact__icon" viewBox="0 0 12 12"><circle cx="6" cy="6" r="5.3" fill="var(--brand-blue)"/><path d="M0.7,6 H11.3 M6,0.7 C3,3.5 3,8.5 6,11.3 M6,0.7 C9,3.5 9,8.5 6,11.3" fill="none" stroke="#fff" stroke-width="0.8"/></svg>
          www.brivoterna-example.com
        </li>
      </ul>
    </div>
  </section>

</main>
</body>
</html>
```